FinTech company looking to revamp and expand client-facing interface for our financial models

Pellworth Engines currently has a very simple website that allows clients to interact with our financial models. We are looking to completely redesign the current site and add several extra pages to provide extra functionality. We want the design to have a modern, slick feel, that will work on both a desktop or a tablet. It should be straightforward for clients to move between different pages at any time, and clear from the layout how to interact with the more advanced features. We have included screenshots of existing pages in the attached design brief, as well as sketches of the functionality required by the new pages, but can't provide a direct link to the current site.
Target Market(s)
Professional investors that will be paying to access the interface
Industry/Entity Type
Finance
Number of Pages Required
4 page
Colors
Designer to choose colors to be used in the design.
Look and feel
Each slider illustrates characteristics of the customer's brand and the style your logo design should communicate.

```html
<!DOCTYPE html>
<html lang="en">
<head>
<meta charset="utf-8">
<title>Pellworth Engines – ETF Pairs Models</title>
<link rel="stylesheet" href="https://fonts.googleapis.com/css2?family=Open+Sans:wght@400;600;700&family=Arimo:wght@400&display=swap">
<style>
  :root {
    --page-bg: #e7e7e7;
    --white: #ffffff;
    --navy: #07325f;
    --ink: #111111;
    --muted-tab: #f4f4f4;
    --teal: #04685f;
    --teal-veil: rgba(18, 112, 106, 0.9);
    --row-alt: #efefef;
    --cell-line: #e0e0e0;
    --filter-head: #686868;
    --drawer: #2a2a2a;
    --tab-active: #1c1c1c;
    --field-border: #c9c9c9;
  }
  * { box-sizing: border-box; margin: 0; padding: 0; }
  html, body { width: 1200px; height: 706px; overflow: hidden; background: var(--page-bg); }
  body { font-family: "Open Sans", Arial, sans-serif; color: var(--ink); }
  .stage { position: relative; width: 1300px; height: 765px; transform: scale(0.923077); transform-origin: 0 0; background: var(--page-bg); }

  /* top bar */
  .topbar { position: absolute; left: 15px; top: 15px; width: 1270px; height: 60px; background: var(--white); display: flex; box-shadow: 0 4px 10px rgba(0,0,0,0.06); }
  .brand { width: 180px; display: flex; align-items: center; padding-left: 58px; font-weight: 700; font-size: 18px; letter-spacing: 0.3px; }
  .range-tab { width: 90px; display: flex; align-items: center; justify-content: center; font-weight: 700; font-size: 14px; border-right: 1px solid #ececec; }
  .range-tab.is-active { background: var(--navy); color: var(--white); border: 0; }
  .spacer { width: 135px; border-right: 1px solid #ececec; }
  .nav-item { display: flex; align-items: center; justify-content: center; gap: 8px; font-weight: 700; font-size: 13px; border-right: 1px solid #ececec; }
  .nav-item.is-active { background: var(--navy); color: var(--white); }
  .nav-item svg { width: 24px; height: 24px; }

  /* workspace */
  .workspace { position: absolute; left: 15px; top: 170px; width: 1270px; height: 580px; background: linear-gradient(#dfdfdf, #f3f3f3 40%, #fafafa); }

  .model-tab { position: absolute; height: 40px; display: flex; align-items: center; justify-content: center; background: var(--muted-tab); font-weight: 600; font-size: 13px; color: #333; border-radius: 4px 4px 0 0; }
  .model-tab.is-raised { background: var(--white); }
  .model-tab.is-active { background: var(--tab-active); color: var(--white); }
  .tab-arrow { position: absolute; left: 1190px; top: 135px; width: 40px; height: 35px; background: var(--white); display: flex; align-items: center; justify-content: center; border-radius: 4px 4px 0 0; }
  .tab-add { position: absolute; left: 1235px; top: 135px; width: 40px; height: 35px; background: var(--navy); display: flex; align-items: center; justify-content: center; border-radius: 4px 4px 0 0; }

  .export { position: absolute; left: 1165px; top: 212px; display: flex; align-items: center; gap: 8px; color: var(--navy); font-weight: 700; font-size: 17px; }

  /* results table */
  .results { position: absolute; left: 105px; top: 250px; width: 1160px; border-collapse: collapse; background: var(--white); box-shadow: 0 2px 8px rgba(0,0,0,0.12); font-family: "Arimo", Arial, sans-serif; font-size: 16px; table-layout: fixed; }
  .results th { height: 70px; background: var(--teal); color: var(--white); font-family: "Open Sans", Arial, sans-serif; font-weight: 700; font-size: 16px; border-right: 1px solid rgba(255,255,255,0.18); }
  .results td { height: 70px; text-align: center; border-right: 1px solid var(--cell-line); padding: 0 4px; line-height: 1.3; }
  .results tr:nth-child(even) td { background: var(--row-alt); }
  .results th:first-child { border-radius: 6px 0 0 0; }
  .results th:last-child { border-radius: 0 6px 0 0; border-right: 0; }
  .results td:last-child { border-right: 0; }

  .filter-veil { position: absolute; left: 15px; top: 170px; width: 490px; height: 430px; background: var(--teal-veil); }

  .filter-drawer { position: absolute; left: 505px; top: 260px; width: 50px; height: 250px; background: var(--drawer); border-radius: 0 4px 4px 0; opacity: 0.95; }
  .filter-drawer span { position: absolute; left: 50%; top: 125px; transform: translate(-50%, -50%) rotate(-90deg); color: var(--white); font-weight: 700; font-size: 15px; letter-spacing: 2px; }
  .drawer-toggle { position: absolute; left: 541px; top: 370px; }

  .filters { position: absolute; left: 75px; top: 245px; width: 370px; height: 280px; background: var(--white); border-radius: 4px; overflow: hidden; box-shadow: 0 4px 12px rgba(0,0,0,0.15); }
  .filters h2 { height: 50px; background: var(--filter-head); color: var(--white); font-size: 18px; font-weight: 700; display: flex; align-items: center; justify-content: center; }
  .filter-row { height: 50px; display: flex; align-items: center; padding-left: 16px; font-size: 17px; border-bottom: 1px solid #ececec; }
  .filter-row .label { width: 85px; }
  .filter-row .label b { font-weight: 700; }
  .filter-row .thr { font-weight: 700; width: 102px; }
  .field { width: 150px; height: 30px; border: 2px solid var(--field-border); border-radius: 5px; padding-left: 10px; display: flex; align-items: center; font-size: 16px; }
  .apply-row { font-weight: 700; }
  .check { display: inline-flex; align-items: center; gap: 8px; margin-left: 18px; }
  .check i { width: 18px; height: 18px; border: 1.5px solid #999; border-radius: 3px; background: #f7f7f7; }
  .search-btn { display: block; margin: 16px auto 0; width: 153px; height: 48px; background: var(--navy); color: var(--white); font-weight: 700; font-size: 15px; border-radius: 4px; display: flex; align-items: center; justify-content: center; }
</style>
</head>
<body>
<div class="stage">

  <header class="topbar">
    <div class="brand">PQUANT</div>
    <div class="range-tab is-active">250D</div>
    <div class="range-tab">83D</div>
    <div class="range-tab">42D</div>
    <div class="spacer"></div>
    <div class="nav-item is-active" style="width:141px">
      <svg viewBox="0 0 24 24" fill="none" stroke="#fff" stroke-width="1.8"><path d="M3 11.5 12 4l9 7.5"/><path d="M5.5 10v10h5v-6h3v6h5V10"/></svg>MODELS</div>
    <div class="nav-item" style="width:177px">
      <svg viewBox="0 0 24 24" fill="#222"><circle cx="12" cy="12" r="2.4"/><circle cx="12" cy="4" r="1.5"/><circle cx="12" cy="20" r="1.5"/><circle cx="4" cy="12" r="1.5"/><circle cx="20" cy="12" r="1.5"/><circle cx="6.3" cy="6.3" r="1.5"/><circle cx="17.7" cy="6.3" r="1.5"/><circle cx="6.3" cy="17.7" r="1.5"/><circle cx="17.7" cy="17.7" r="1.5"/><circle cx="12" cy="8" r="1"/><circle cx="12" cy="16" r="1"/><circle cx="8" cy="12" r="1"/><circle cx="16" cy="12" r="1"/></svg>SENSITIVITIES</div>
    <div class="nav-item" style="width:160px">
      <svg viewBox="0 0 24 24" fill="none" stroke="#222" stroke-width="1.8"><circle cx="7" cy="7" r="4"/><circle cx="17" cy="7" r="4"/><circle cx="7" cy="17" r="4"/><circle cx="17" cy="17" r="4"/></svg>PORTFOLIO</div>
    <div class="nav-item" style="width:152px">
      <svg viewBox="0 0 24 24" fill="none" stroke="#222" stroke-width="1.8"><rect x="3" y="4" width="18" height="16"/><path d="M3 8h18"/><path d="M6 17l4-5 3 3 5-5"/></svg>BACKTEST</div>
  </header>

  <div class="workspace"></div>

  <nav>
    <div class="model-tab" style="left:70px;top:135px;width:155px;height:35px">EQUITIES</div>
    <div class="model-tab" style="left:230px;top:135px;width:155px;height:35px">ETFS</div>
    <div class="model-tab is-raised" style="left:390px;top:125px;width:155px;height:45px">PAIRS</div>
    <div class="model-tab is-active" style="left:550px;top:115px;width:155px;height:55px">ETF PAIRS</div>
    <div class="model-tab is-raised" style="left:710px;top:125px;width:155px;height:45px">FACTORS</div>
    <div class="model-tab is-raised" style="left:870px;top:135px;width:155px;height:35px">NEW TAB TITLE #1</div>
    <div class="model-tab is-raised" style="left:1030px;top:135px;width:155px;height:35px">NEW TAB TITLE #2</div>
    <div class="tab-arrow"><svg width="14" height="20" viewBox="0 0 14 20"><path d="M3 2l8 8-8 8" fill="none" stroke="#aaa" stroke-width="3"/></svg></div>
    <div class="tab-add"><svg width="24" height="24" viewBox="0 0 24 24" fill="none" stroke="#fff" stroke-width="1.8"><circle cx="12" cy="12" r="10"/><path d="M12 7v10M7 12h10"/></svg></div>
  </nav>

  <div class="export">
    <svg width="26" height="24" viewBox="0 0 26 24" fill="none" stroke="#07325f" stroke-width="2.2"><path d="M11 5H3v16h16v-6"/><path d="M8 16c1-6 6-9 13-9"/><path d="M17 3l4 4-4 4"/></svg>Export</div>

  <table class="results">
    <colgroup>
      <col style="width:100px"><col style="width:140px"><col style="width:115px"><col style="width:85px">
      <col style="width:90px"><col style="width:90px"><col style="width:90px"><col style="width:90px">
      <col style="width:90px"><col style="width:90px"><col style="width:90px"><col style="width:90px">
    </colgroup>
    <thead>
      <tr><th>Model</th><th>Sector</th><th>Date</th><th>Quality</th><th>Stat 1</th><th>Stat 2</th><th>Stat 3</th><th>Stat 4</th><th>Stat 5</th><th>Stat 6</th><th>Stat 7</th><th>Stat 8</th></tr>
    </thead>
    <tbody>
      <tr><td>Model 1</td><td>Information Technology</td><td>2019-07-03 12:15:00.000</td><td>30.2282</td><td>2.01574</td><td>23.305</td><td>-0.149368</td><td>22.3054</td><td>4.63714</td><td>0.945706</td><td>2.81949</td><td>2.60858</td></tr>
      <tr><td>Model 2</td><td>Information Technology</td><td>2019-07-03 12:15:00.000</td><td>32.8694</td><td>0.87307</td><td>32.185</td><td>-0.033692</td><td>33.9911</td><td>11.5693</td><td>-0.472968</td><td>-0.830458</td><td>6.80646</td></tr>
      <tr><td>Model 3</td><td>Information Technology</td><td>2019-07-03 12:15:00.000</td><td>1.66002</td><td>-0.569222</td><td>159.814</td><td>0.0252328</td><td>172.616</td><td>10.2875</td><td>-0.750396</td><td>-0.385309</td><td>4.69146</td></tr>
      <tr><td>Model 4</td><td>Information Technology</td><td>2019-07-03 12:15:00.000</td><td>45.6856</td><td>0.412148</td><td>202.488</td><td>0.0084923</td><td>205.834</td><td>11.9094</td><td>-0.137913</td><td>0.449595</td><td>3.85106</td></tr>
      <tr><td>Model 5</td><td>Information Technology</td><td>2019-07-03 12:15:00.000</td><td>75.7733</td><td>7.06728</td><td>188.605</td><td>0.016913</td><td>161.665</td><td>3.82241</td><td>0.981019</td><td>1.29847</td><td>3.34927</td></tr>
    </tbody>
  </table>

  <div class="filter-veil"></div>

  <div class="filter-drawer"><span>FILTERS</span></div>
  <svg class="drawer-toggle" width="28" height="28" viewBox="0 0 28 28"><circle cx="14" cy="14" r="12.5" fill="#fff" stroke="#07325f" stroke-width="2"/><path d="M20 14H9M13 9.5 8.5 14l4.5 4.5" fill="none" stroke="#07325f" stroke-width="2.2"/></svg>

  <section class="filters">
    <h2>Filters</h2>
    <div class="filter-row"><span class="label">Quality</span><span class="thr">Threshold:</span><span class="field">-10</span></div>
    <div class="filter-row"><span class="label"><b>Abs.</b> Stat</span><span class="thr">Threshold:</span><span class="field">-10</span></div>
    <div class="filter-row apply-row">Apply <span class="check"><i></i>All tabs</span><span class="check"><i></i>Current tab</span></div>
    <div class="search-btn">SEARCH</div>
  </section>

</div>
</body>
</html>
```